Need a design for coffee shop/bar

We need a simple site designed for a local coffee shop and bar. Small, locally owned place. Has live entertainment on occasion. Serves the business lunch and happy hour crowd as well and the baseball and basketball games fans. Located in downtown Cleveland. Looking for a simple site design with logo at top, horizontal main nav and slideshow and will need an interior page design as well (which will be used for general content like about, contact, menu, events, etc.) Would like it to be responsive. Current site is bvmelkins.com. Owner likes the color scheme, but open to changes.

*note - the owner roasts his own coffee and has a sister company for this called Harrow Bean Works (harrowbeanworks.com). We plan to use the exact same design for the coffee company's website, expect we'll swap out the logo at the top and use different photos. As part of the project we'd like a page designed that displays the various coffee products, but do not require this specific site be designed.

So, that makes three pages total. Home page (bvmelkins.com), interior and product page.

Target Market(s)

Young professionals, hipsters, sports fans, coffee and beer enthusiasts. Owner is into reggae and often has reggae bands.

Industry/Entity Type

Entertainment

Number of Pages Required

3 page

Requirements
Must have
• Slideshow, lot of images (some examples are on the current site, bvmelkins.com - client will be providing us with higher resolution images when we start development, so place holders are fine for the design). Responsive.

```html
<!DOCTYPE html>
<html lang="en">
<head>
<meta charset="utf-8">
<title>B.V. Melkin's – Coffee &amp; Bar</title>
<link href="https://fonts.googleapis.com/css2?family=Raleway:wght@400;500;600&family=Open+Sans:wght@400;600&family=Libre+Baskerville&display=swap" rel="stylesheet">
<style>
:root{
  --bg:#000;
  --bg-soft:#111;
  --bg-band:#2b2b2b;
  --gold:#f7a90e;
  --gold-light:#ffc21a;
  --orange-deep:#f08a05;
  --brown:#7a3510;
  --brown-dark:#5a2408;
  --text:#fff;
  --text-soft:#cfcfcf;
  --text-dim:#a8a8a8;
}
*{box-sizing:border-box;margin:0;padding:0}
html,body{width:964px;height:1200px;overflow:hidden;background:var(--bg)}
body{position:relative;font-family:"Open Sans",sans-serif;color:var(--text)}
.abs{position:absolute}
.page-top{left:0;top:0;width:964px;height:130px;background:radial-gradient(ellipse at 50% 30%,#1c1c1c,#000 75%)}
.scallops{left:0;top:0}
.brand{left:164px;top:44px;font-family:"Raleway",sans-serif;font-weight:600;font-size:25px;letter-spacing:1px;color:var(--gold)}
.order{right:166px;top:43px;text-align:right;font-family:"Libre Baskerville",serif}
.order-label{font-size:12px;color:var(--gold);letter-spacing:.5px}
.order-phone{font-size:17px;color:var(--text);display:flex;align-items:center;gap:5px;justify-content:flex-end;margin-top:2px}
.main-nav{left:161px;top:90px;width:641px;height:36px;background:linear-gradient(#ffbe14,#f59a06);display:flex;font-family:"Raleway",sans-serif;font-size:12px;font-weight:500}
.main-nav a{color:var(--text);text-decoration:none;line-height:36px;padding:0 18.5px}
.main-nav a.active{background:linear-gradient(#8a3a0e,#5e2608);padding:0 23px;margin-right:4px}
.hero{left:162px;top:126px}
.hero-caption{left:333px;top:202px;width:292px;height:102px;background:rgba(60,45,20,.72);text-align:center;font-family:"Raleway",sans-serif}
.hero-caption h2{font-weight:400;font-size:21px;line-height:24px;margin-top:15px}
.hero-caption h2 span{font-size:23px}
.hero-caption p{font-family:"Open Sans",sans-serif;font-size:7.3px;line-height:13.5px;color:#d9d1c2;margin-top:6px}
.dots{left:453px;top:374px;display:flex;gap:4px}
.dots i{width:11px;height:11px;border-radius:50%;background:#eee;display:block}
.welcome{left:162px;top:442px;width:404px}
.welcome h1{font-family:"Raleway",sans-serif;font-weight:400;font-size:20.5px;margin-bottom:8px}
.welcome p{font-size:7.5px;line-height:13.6px;color:var(--text-soft);margin-bottom:8px}
.menu-card{left:578px;top:430px;width:226px;height:190px}
.menu-card svg{position:absolute;left:0;top:0}
.menu-body{position:absolute;left:0;top:0;width:226px;text-align:center;color:#3a1a02}
.menu-body h3{font-family:"Raleway",sans-serif;font-weight:500;font-size:18px;color:var(--text);margin-top:17px;letter-spacing:.5px}
.menu-body h4{font-family:"Raleway",sans-serif;font-size:8.8px;font-weight:600;margin-top:8px;margin-bottom:2px}
.menu-body li{list-style:none;font-size:7.3px;line-height:16.4px}
.view-all{left:656px;top:588px;width:70px;height:20px;border-radius:10px 10px 0 0;background:var(--brown-dark);color:var(--text);font-family:"Raleway",sans-serif;font-size:9.5px;text-align:center;line-height:21px}
.divider{left:170px;top:641px;width:622px;height:3px;background:#1e1e1e}
.divider-knot{left:475px;top:639px;width:11px;height:6px;border:1px solid #444;background:#000}
.feature{top:673px;width:210px}
.feature-photo{display:block;width:204px;height:108px;border:2px solid #eee;border-radius:4px 22px 4px 4px}
.feature h3{font-family:"Raleway",sans-serif;font-weight:400;font-size:17.5px;color:var(--gold);margin:8px 0 8px 7px}
.feature p{font-size:7.6px;line-height:13.6px;color:var(--text-soft);margin-left:7px;height:58px}
.btn{display:inline-block;margin-left:6px;width:72px;height:25px;border-radius:13px;background:linear-gradient(#ffc21a,#f39305);color:var(--text);font-family:"Raleway",sans-serif;font-size:9px;text-align:center;line-height:25px}
.footer-info{left:0;top:934px;width:964px;height:190px;background:var(--bg-soft)}
.footer-info h3{position:absolute;font-family:"Raleway",sans-serif;font-weight:400;font-size:16px}
.hours-col{position:absolute;top:993px;font-size:8.5px;line-height:16.5px;color:var(--text-dim)}
.contact{left:638px;top:989px;font-size:8.6px;line-height:16.5px;color:var(--text-dim)}
.contact .name{font-size:11px;color:#c8c8c8;margin-bottom:1px}
.footer-band{left:0;top:1090px}
.footer-nav{left:162px;top:1133px;font-family:"Raleway",sans-serif;font-size:8.8px;font-weight:600;color:var(--text)}
.footer-nav span{color:#ccc;margin:0 4px}
.copyright{left:162px;top:1154px;font-size:7.8px;color:#9a9a9a}
.social{left:726px;top:1132px;display:flex;gap:9px}
.social i{display:block;width:16px;height:16px;border-radius:50%;background:#fff}
</style>
</head>
<body>

<div class="abs page-top"></div>
<svg class="abs scallops" width="964" height="14" aria-hidden="true">
  <defs>
    <pattern id="tab" width="32" height="14" patternUnits="userSpaceOnUse">
      <rect x="4" y="-8" width="19" height="21" rx="7" fill="#3a3a3a"/>
    </pattern>
  </defs>
  <rect width="964" height="14" fill="url(#tab)"/>
</svg>

<header>
  <div class="abs brand">B.V. MELKIN'S</div>
  <div class="abs order">
    <div class="order-label">ORDER NOW</div>
    <div class="order-phone">
      <svg width="13" height="13" viewBox="0 0 24 24" aria-hidden="true"><path fill="#f7a90e" d="M6.6 10.8a15.1 15.1 0 0 0 6.6 6.6l2.2-2.2c.3-.3.7-.4 1-.2 1.1.4 2.3.6 3.6.6.6 0 1 .4 1 1V20c0 .6-.4 1-1 1A17 17 0 0 1 3 4c0-.6.4-1 1-1h3.5c.6 0 1 .4 1 1 0 1.3.2 2.5.6 3.6.1.3 0 .7-.2 1z"/></svg>
      555.861.0142
    </div>
  </div>
  <nav class="abs main-nav">
    <a class="active">HOME</a><a>ABOUT US</a><a>MENU</a><a>HOURS</a><a>SPECIALS</a><a>BLOG</a><a>CONTACT US</a>
  </nav>
</header>

<section>
  <svg class="abs hero" width="641" height="284" role="img" aria-label="Slideshow photo: a cup of steaming coffee on a saucer beside roasted coffee beans on a wooden table">
    <defs>
      <linearGradient id="heroFill" x1="0" y1="0" x2="0" y2="1">
        <stop offset="0" stop-color="#2a1408"/>
        <stop offset=".45" stop-color="#5a3218"/>
        <stop offset=".75" stop-color="#3a1c0c"/>
        <stop offset="1" stop-color="#7a5238"/>
      </linearGradient>
      <radialGradient id="heroGlow" cx=".78" cy=".6" r=".35">
        <stop offset="0" stop-color="#e8e2d6" stop-opacity=".55"/>
        <stop offset="1" stop-color="#e8e2d6" stop-opacity="0"/>
      </radialGradient>
    </defs>
    <path d="M0 0H641V283C500 268 300 292 0 270Z" fill="url(#heroFill)"/>
    <path d="M0 0H641V283C500 268 300 292 0 270Z" fill="url(#heroGlow)"/>
    <path d="M0 270C300 292 500 268 641 283" fill="none" stroke="#8a8a8a" stroke-width="1"/>
  </svg>
  <div class="abs hero-caption">
    <h2>Its a Perfect Spot to host<br><span>your Gathering!</span></h2>
    <p>Class aptent taciti sociosqu ad litora torquent per conubia nostra<br>per inceptos hymenaeos Proin nulla arcu nonummy</p>
  </div>
  <div class="abs dots"><i></i><i></i><i></i><i></i></div>
</section>

<section class="abs welcome">
  <h1>Welcome to BV Melkin's Mainpage</h1>
  <p>B.V. Melkin's proudly owns and operates the Harrow Bean Works. We have been roasting coffee for B.V. Melkin's and a number of local accounts since 2003. We select the finest arabica beans from around the world and practice buying methods that support fair wage and earth friendly growing methods. We have composted mutiple tons of spent coffee grounds to local organic farmers and community gardens.</p>
  <p>We prepare and bake all the good eats. We feature healthy choices. We pour a fresh pint. We roast our own coffee. We buy locally. We recycle. Join us in the morning. B.V. Melkin's features breakfast sandwiches, bakery and pastries. At lunch, we proudly serve freshly sliced Stonegate Deli on open grain oven baked sandwiches, flat bread pizzas, soups and salads and veggie choices.</p>
</section>

<aside class="abs menu-card">
  <svg width="226" height="190" aria-hidden="true">
    <defs>
      <linearGradient id="menuFill" x1="0" y1="0" x2="0" y2="1">
        <stop offset="0" stop-color="#ffbe14"/>
        <stop offset="1" stop-color="#f28a04"/>
      </linearGradient>
    </defs>
    <path d="M0 8Q0 0 8 0H218Q226 0 226 8V174Q113 198 0 174Z" fill="#9a4508"/>
    <path d="M0 8Q0 0 8 0H218Q226 0 226 8V160Q113 178 0 160Z" fill="url(#menuFill)"/>
  </svg>
  <div class="menu-body">
    <h3>OUR MENU</h3>
    <h4>DAILY SPECIALS</h4>
    <ul>
      <li>Monday - Turkey Club w side $6.75</li>
      <li>Tuesday - Tuna Melt w side $6.50</li>
      <li>Wednesday - The Jake w side $6.50</li>
      <li>Thursday - Corned Beef or Turkey Reubens w side $7</li>
      <li>Friday - Grilled Cheese and Tomato Soup $6</li>
    </ul>
  </div>
</aside>
<div class="abs view-all">View all</div>

<div class="abs divider"></div>
<div class="abs divider-knot"></div>

<section>
  <article class="abs feature" style="left:161px">
    <div class="feature-photo" role="img" aria-label="Photo: crowd and bicycles outside the cafe on a busy street" style="background:linear-gradient(160deg,#6a6058,#3a3430 45%,#7a5a48 80%,#4a4038)"></div>
    <h3>Parking Tips</h3>
    <p>Meter Parking on Linden or Carver.<br>Lots - Directly behind BVM on Pell Alley.<br>Garage/lots will have a fee whenever Lakefront Field has a game and every time the Arena has an event.</p>
    <span class="btn">Read More</span>
  </article>
  <article class="abs feature" style="left:378px">
    <div class="feature-photo" role="img" aria-label="Photo: candlelit tables with white tablecloths in the dining room" style="background:radial-gradient(ellipse at 55% 70%,#c8b8c8,#6a4a60 35%,#2a1420 75%)"></div>
    <h3 style="margin-left:8px">Why Choose Us</h3>
    <p style="margin-left:10px">We prepare and bake all the good eats. We feature healthy choices. We pour a fresh pint. We roast our own coffee. We buy locally. Join us in the morning. B.V. Melkin's features breakfast sandwiches</p>
    <span class="btn" style="margin-left:10px">Read More</span>
  </article>
  <article class="abs feature" style="left:597px">
    <div class="feature-photo" role="img" aria-label="Photo: cafe storefront windows with patio chairs at dusk" style="background:linear-gradient(100deg,#3a2a18,#a07840 30%,#5a4020 55%,#b08850 80%,#3a2810)"></div>
    <h3 style="margin-left:10px">Order Now</h3>
    <p style="margin-left:12px">Pellentesque faucibus Ut accumsan ultricies elit Maecenas at justo id velit placerat molestie Donec dictum lectus non odio Cras a ante vitae enim iaculis aliquam Mauris nunc quam venenatis</p>
    <span class="btn" style="margin-left:12px">Read More</span>
  </article>
</section>

<footer>
  <div class="abs footer-info">
    <h3 style="left:169px;top:30px">Open Hours</h3>
    <h3 style="left:636px;top:26px">Contact Info</h3>
  </div>
  <div class="hours-col" style="left:170px">Monday 7am - 9pm<br>Tue - Fri 7a - midnight<br>Sat - 8am - midnight<br>Sun - 8am - 2pm</div>
  <div class="hours-col" style="left:295px">HAPPY HOUR:<br>Monday - Happy Hour all night!<br>Tue - Fri - 4pm to 7pm</div>
  <div class="hours-col" style="left:446px">Evening food and drink specials...<br>Thursday-$3.5 Pints of Harbor Stout,<br>Fenwick Lager, Lakeshore Ale<br>Friday-$6 Irish coffee and Martinis</div>
  <div class="abs contact">
    <div class="name">B.V. Melkin's</div>
    412 Larch Street Millbrook, OH 44987<br>
    Email: Dana@bvmelkins.com<br>
    Phone: 555.861.0142
  </div>

  <svg class="abs footer-band" width="964" height="110" aria-hidden="true">
    <path d="M0 28C300 -2 650 0 964 12V110H0Z" fill="#2b2b2b"/>
  </svg>
  <nav class="abs footer-nav">HOME<span>|</span>ABOUT US<span>|</span>MENU<span>|</span>HOURS<span>|</span>SPECIALS<span>|</span>BLOG<span>|</span>CONTACT US</nav>
  <div class="abs copyright">© 2015 Company Name &nbsp;All right reserved &nbsp;Term of Use</div>
  <div class="abs social" aria-hidden="true"><i></i><i></i><i></i></div>
</footer>

</body>
</html>
```